Sophisticated, clean website reflecting my feminine, playful side to sell my abstract art,

I need a website no more than 3 pages to showcase my paintings, a little about me and some contact info. I do abstracts so looking for something a little edgy, yet feminine and current.
Updates

Hi there, These are some artists websites that I Iike: Marnelvoss.com (I like how airy it is) peterwallombry.com garethpolvens.com (I like how it scrolls) I'll need a place for a photo ( a headshot-i do not have it yet so I'll need to be able to upload that later) as well as an area for my bio. Also, it's important that I will be able to upload any new photos and descriptions easily so it should be user friendly. Lastly, I like in a sunny place so would like to have this seem upbeat and playful as that is how i like to paint. thanks-I'm trying to upload my photos now -

Target Market(s)

ppl ages 35-70 who want large scale art for their homes

Industry/Entity Type

art

Coding

Coded - Design and coding required

Number of Pages Required

3 page

Colors

Designer to choose colors to be used in the design.

Requirements
Must have
• photos of my art, a place for my bio, be easy to reach me. tasteful-nothing too "in your face" -my clients are pretty high end and organized. They like clean lines
Nice to have
• sophisticated background, muted tones in the back-similar clean font throughout-no cursive
Should not have
• too many dark areas. Too many blocks of color. Too serious.

```html
<!DOCTYPE html>
<html lang="en">
<head>
<meta charset="utf-8">
<title>Delia Marsh — Abstract Art</title>
<link rel="stylesheet" href="https://fonts.googleapis.com/css2?family=Raleway:wght@300;400&family=Nunito+Sans:wght@300;400&family=Quicksand:wght@400;500&display=swap">
<style>
  :root {
    --ink: #3b3b3b;
    --ink-soft: #555555;
    --line: #bdbdbd;
    --line-soft: #d6d6d6;
    --paper: #ffffff;
    --hero-a: #e9e5dc;
    --hero-b: #ddcfa6;
    --hero-c: #cfd5df;
    --art-a: #3f8c5b;
    --art-b: #5a9f58;
    --art-c: #2f7266;
    --portrait-a: #f1f1f1;
    --portrait-b: #e6e6e6;
  }
  * { box-sizing: border-box; margin: 0; padding: 0; }
  html, body { width: 1200px; height: 2928px; overflow: hidden; background: var(--paper); }
  body { position: relative; color: var(--ink); font-family: "Nunito Sans", sans-serif; }

  .brand {
    position: absolute; top: 22px; left: 0; width: 1200px; text-align: center;
    font-family: "Raleway", sans-serif; font-weight: 300; font-size: 44px;
    letter-spacing: 3px; color: var(--ink-soft);
  }
  .rule { position: absolute; left: 0; width: 1200px; height: 1px; background: var(--line); }

  .main-nav a {
    position: absolute; top: 116px; transform: translateX(-50%);
    font-family: "Quicksand", sans-serif; font-size: 16px; color: var(--ink);
    text-decoration: none; letter-spacing: 0.3px; white-space: nowrap;
  }
  .main-nav a.is-active::after {
    content: ""; position: absolute; left: 0; right: 0; top: 27px; height: 2px; background: var(--ink);
  }

  .hero {
    position: absolute; top: 158px; left: 0; width: 1200px; height: 658px;
    background: linear-gradient(120deg, var(--hero-a), var(--hero-b) 45%, var(--hero-c) 80%, var(--hero-a));
  }
  .slider-arrow { position: absolute; }

  .section-title {
    position: absolute; left: 0; width: 1200px; text-align: center;
    font-family: "Raleway", sans-serif; font-weight: 300; font-size: 46px; color: var(--ink);
  }
  .title-bar { position: absolute; left: 568px; width: 64px; height: 3px; background: var(--ink); }

  .portrait-frame {
    position: absolute; left: 93px; top: 1019px; width: 307px; height: 309px;
    border: 1px solid var(--line-soft); border-radius: 6px; padding: 8px; background: var(--paper);
  }
  .portrait { width: 100%; height: 100%; background: linear-gradient(180deg, var(--portrait-a), var(--portrait-b)); }

  .bio {
    position: absolute; left: 436px; top: 1020px; width: 712px;
    font-size: 19px; font-weight: 300; line-height: 32px; color: var(--ink);
  }
  .bio p + p { margin-top: 14px; }

  .artwork-frame {
    position: absolute; left: 156px; top: 1623px; width: 885px; height: 562px;
    border: 2px solid var(--line); border-radius: 8px; padding: 7px; background: var(--paper);
  }
  .artwork {
    width: 100%; height: 100%; border-radius: 6px;
    background: linear-gradient(135deg, var(--art-a), var(--art-b) 50%, var(--art-c));
  }

  .contact-lead {
    position: absolute; top: 2450px; left: 0; width: 1183px; text-align: center;
    font-size: 21px; font-weight: 300; color: var(--ink);
  }
  .contact-item {
    position: absolute; top: 2513px; width: 236px; height: 236px;
    border: 1.5px solid var(--line); border-radius: 50%;
    font-family: "Quicksand", sans-serif; font-size: 17px; color: var(--ink);
    text-align: center;
  }
  .contact-item svg, .contact-item .mark { position: absolute; left: 50%; top: 70px; transform: translateX(-50%); }
  .contact-item .mark { width: 34px; height: 34px; border: 1.5px solid var(--ink); border-radius: 50%; top: 74px; }
  .contact-item span { position: absolute; left: 0; right: 0; top: 130px; white-space: nowrap; }

  .footer-note {
    position: absolute; top: 2874px; left: 0; width: 1230px; text-align: center;
    font-family: "Quicksand", sans-serif; font-size: 14px; color: var(--ink-soft);
  }
</style>
</head>
<body>
  <header>
    <div class="brand">DELIA MARSH</div>
    <div class="rule" style="top:99px"></div>
    <nav class="main-nav">
      <a href="#" class="is-active" style="left:270px">HOME</a>
      <a href="#" style="left:449px">ABOUT ME</a>
      <a href="#" style="left:640px">GALLERY</a>
      <a href="#" style="left:828px">CONTACT</a>
    </nav>
  </header>

  <section class="hero" role="img" aria-label="Featured abstract painting">
    <svg class="slider-arrow" style="left:22px;top:282px" width="30" height="56" viewBox="0 0 30 56"><polyline points="26,4 4,28 26,52" fill="none" stroke="#fff" stroke-width="4"/></svg>
    <svg class="slider-arrow" style="left:1136px;top:282px" width="30" height="56" viewBox="0 0 30 56"><polyline points="4,4 26,28 4,52" fill="none" stroke="#fff" stroke-width="4"/></svg>
  </section>

  <section class="about">
    <h2 class="section-title" style="top:914px">ABOUT ME</h2>
    <div class="title-bar" style="top:975px"></div>
    <div class="portrait-frame"><div class="portrait" role="img" aria-label="Headshot portrait of the artist"></div></div>
    <div class="bio">
      <p>Lorem ipsum dolor sit amet, consectetur adipiscing elit, sed do eiusmod tempor in­cididunt ut labore et dolore magna aliqua. Ut enim ad minim veniam, quis nostrud ex­ercitation Lorem ipsum dolor sit amet, consectetur adipiscing elit, sed do eiusmod tempor incididunt ut labore et dolore magna aliqua.</p>
      <p>Duis aute irure dolor in reprehenderit in voluptate velit esse cillum dolore eu fugiat nulla pariatur. Excepteur sint occaecat cupidatat non proident, sunt in culpa qui officia deserunt mollit anim id est laborum.Sed ut perspiciatis unde pariatur. Excepteur sint occaecat cupidatat non proident, sunt in culpa qui officia deserunt mollit anim id est laborum.Sed ut persmollit anim id est laborum.Sed ut perspiciatis unde pariatur</p>
    </div>
  </section>

  <div class="rule" style="top:1446px"></div>

  <section class="gallery">
    <h2 class="section-title" style="top:1514px">GALLERY</h2>
    <div class="title-bar" style="top:1575px"></div>
    <svg class="slider-arrow" style="left:86px;top:1880px" width="30" height="48" viewBox="0 0 30 48"><polyline points="26,3 5,24 26,45" fill="none" stroke="#777" stroke-width="3.5"/></svg>
    <div class="artwork-frame"><div class="artwork" role="img" aria-label="Gallery abstract painting"></div></div>
    <svg class="slider-arrow" style="left:1085px;top:1880px" width="30" height="48" viewBox="0 0 30 48"><polyline points="4,3 25,24 4,45" fill="none" stroke="#777" stroke-width="3.5"/></svg>
  </section>

  <div class="rule" style="top:2285px"></div>

  <section class="contact">
    <h2 class="section-title" style="top:2365px">CONTACT US</h2>
    <div class="title-bar" style="top:2426px"></div>
    <p class="contact-lead">Please get in touch with me on below details.</p>

    <div class="contact-item" style="left:115px">
      <svg width="40" height="30" viewBox="0 0 40 30" style="top:80px"><rect x="1" y="1" width="38" height="28" fill="none" stroke="#3b3b3b" stroke-width="1.5"/><polyline points="1,1 20,17 39,1" fill="none" stroke="#3b3b3b" stroke-width="1.5"/><path d="M1 29 L15 13 M25 13 L39 29" fill="none" stroke="#3b3b3b" stroke-width="1.5"/></svg>
      <span>info@deliamarsh.com</span>
    </div>
    <div class="contact-item" style="left:363px">
      <svg width="40" height="40" viewBox="0 0 40 40"><path d="M8 3 L14 3 L17 12 L12 15 C14 21 19 26 25 28 L28 23 L37 26 L37 32 C37 35 35 37 32 37 C17 36 4 23 3 8 C3 5 5 3 8 3 Z" fill="none" stroke="#3b3b3b" stroke-width="1.5"/><path d="M23 10 A8 8 0 0 1 30 17 M23 4 A14 14 0 0 1 36 17" fill="none" stroke="#3b3b3b" stroke-width="1.5"/></svg>
      <span>(123) 456 7890</span>
    </div>
    <div class="contact-item" style="left:610px">
      <div class="mark"></div>
      <span>@dmarshart</span>
    </div>
    <div class="contact-item" style="left:857px">
      <div class="mark"></div>
      <span>@dmpainter</span>
    </div>
  </section>

  <footer>
    <div class="rule" style="top:2855px"></div>
    <p class="footer-note">© 2022 Delia Marsh &nbsp; All Rights Reserved</p>
  </footer>
</body>
</html>
```